Mobile Fitness snd Therapy Business Card Design

I need a business card designed for my mobile fitness and therapy business.

Please view the images that I have uploaded. I like the simplicity of the design that I have attached. I adapted it with my information

Target Market(s)

Those seeking personal training, injury rehabilitation or massage therapy.

Industry/Entity Type

Business

Contact Information for Business Card

Derek Fulham - MSc, CAT(C), RMT, CSCS, Pn2
e-mail: derek@vantrelo.com
website: www.vantrelo.com
instagram: @derek_fulham

Font styles to use
Sans Serif

Colors
3176b5
0355a3

Requirements
Must have
• "Contact us to receive a FREE assessment"
• Services offered:
• Personal Training
• Golf Fitness
• Injury Rehab
• Massage Therapy
• Yoga
Nice to have
• Consistent colours with brand
• - Dark Blue: #232837
• - Blue: #5096f0
• Consistent look/feel with the website: www.vantrelo.com

```html
<!DOCTYPE html>
<html lang="en">
<head>
<meta charset="utf-8">
<title>Vantrelo Business Card</title>
<link rel="stylesheet" href="https://fonts.googleapis.com/css2?family=Montserrat:wght@700;800&family=Roboto:wght@400;500&family=Roboto+Condensed:wght@700&display=swap">
<style>
  :root {
    --bg: #e6e4e0;
    --card-white: #f4f4f4;
    --navy: #232837;
    --blue: #2b5fd9;
    --blue-light: #5096f0;
    --text-gray: #4a4d55;
    --divider: #c9c9c9;
    --sep: #6b7180;
    --white: #ffffff;
  }
  * { margin: 0; padding: 0; box-sizing: border-box; }
  html, body { width: 1200px; height: 960px; overflow: hidden; background: var(--bg); }
  .canvas { position: relative; width: 1200px; height: 960px; }

  .card {
    position: absolute;
    width: 600px;
    height: 344px;
    border-radius: 22px;
    overflow: hidden;
    box-shadow: 0 3px 8px rgba(0,0,0,0.25);
  }

  /* Front */
  .card-front { left: 314px; top: 113px; background: var(--card-white); }
  .brand {
    position: absolute;
    text-align: left;
    font-family: "Montserrat", sans-serif;
    font-weight: 800;
    color: var(--navy);
  }
  .card-front .brand { left: 72px; top: 140px; }
  .brand-name { display: block; letter-spacing: 2px; line-height: 1; }
  .card-front .brand-name { font-size: 31px; }
  .brand-tagline {
    display: block;
    font-weight: 700;
    letter-spacing: 1.6px;
    line-height: 1;
  }
  .card-front .brand-tagline { font-size: 10.5px; margin-top: 9px; }

  .divider {
    position: absolute; left: 331px; top: 108px;
    width: 1.5px; height: 114px;
    background: linear-gradient(to bottom, transparent, var(--divider) 20%, var(--divider) 80%, transparent);
  }
  .contact { position: absolute; left: 359px; top: 114px; }
  .person-name {
    font-family: "Roboto Condensed", sans-serif;
    font-weight: 700; font-size: 23px;
    color: var(--blue); line-height: 1;
  }
  .credentials {
    font-family: "Roboto Condensed", sans-serif;
    font-weight: 700; font-size: 10px;
    color: var(--blue); margin-top: 5px;
  }
  .contact-list { list-style: none; margin-top: 20px; }
  .contact-list li {
    display: flex; align-items: center; gap: 8px;
    font-family: "Roboto", sans-serif; font-size: 14.5px;
    color: var(--text-gray); height: 20px;
  }
  .contact-list svg { width: 14px; height: 14px; flex: none; }

  .stripe-blue {
    position: absolute; left: 0; top: 324px;
    width: 420px; height: 8px; background: var(--blue);
  }
  .band-web {
    position: absolute; right: 0; top: 313px;
    width: 191px; height: 31px;
    background: var(--navy);
    clip-path: polygon(18px 0, 100% 0, 100% 100%, 0 100%);
    font-family: "Roboto", sans-serif; font-size: 13.5px;
    color: var(--white);
    display: flex; align-items: center; padding-left: 30px;
  }

  /* Back */
  .card-back { left: 311px; top: 472px; background: var(--navy); text-align: center; }
  .card-back .brand {
    left: 0; right: 0; top: 128px; text-align: center; color: var(--white);
  }
  .card-back .brand-name { font-size: 46px; letter-spacing: 4px; }
  .card-back .brand-tagline { font-size: 15px; letter-spacing: 2.4px; margin-top: 14px; }

  .cta {
    position: absolute; left: 58px; top: 258px;
    width: 483px; height: 33px;
    border-radius: 17px; background: var(--blue);
    font-family: "Roboto Condensed", sans-serif; font-weight: 700;
    font-size: 20px; color: var(--white);
    display: flex; align-items: center; justify-content: center;
  }
  .services {
    position: absolute; left: 0; right: 0; top: 297px;
    list-style: none; display: flex; justify-content: center;
    font-family: "Roboto", sans-serif; font-size: 14.5px; color: var(--white);
  }
  .services li + li::before { content: "|"; color: var(--sep); margin: 0 5px; }
</style>
</head>
<body>
<main class="canvas">
  <section class="card card-front" aria-label="Card front">
    <div class="brand">
      <span class="brand-name">VANTRELO</span>
      <span class="brand-tagline">NUTRITION - FITNESS - HEALTH</span>
    </div>
    <div class="divider"></div>
    <div class="contact">
      <h1 class="person-name">DEREK FULHAM</h1>
      <p class="credentials">MSC, CAT(C), RMT, CSCS, PN2</p>
      <ul class="contact-list">
        <li>
          <svg viewBox="0 0 14 14" aria-hidden="true"><rect x="1" y="3" width="12" height="8.5" rx="1" fill="#2b5fd9"/><path d="M1.5 3.6 L7 7.8 L12.5 3.6" fill="none" stroke="#fff" stroke-width="1.2"/></svg>
          derek@vantrelo.com
        </li>
        <li>
          <svg viewBox="0 0 14 14" aria-hidden="true"><circle cx="7" cy="7" r="6.5" fill="#2b5fd9"/></svg>
          @derek_fulham
        </li>
      </ul>
    </div>
    <div class="stripe-blue"></div>
    <div class="band-web">www.vantrelo.com</div>
  </section>

  <section class="card card-back" aria-label="Card back">
    <div class="brand">
      <span class="brand-name">VANTRELO</span>
      <span class="brand-tagline">NUTRITION - FITNESS - HEALTH</span>
    </div>
    <p class="cta">CONTACT US TO RECEIVE A FREE ASSESSMENT</p>
    <ul class="services">
      <li>Personal Training</li>
      <li>Golf Fitness</li>
      <li>Injury Rehab</li>
      <li>Massage Therapy</li>
      <li>Yoga</li>
    </ul>
  </section>
</main>
</body>
</html>
```